Satchel & Sundial needs new business card design

I need a new business card design. I'm looking for out-of-the-box design which represents the freedom of being a location independent entrepreneur.
I offer coaching, retreats and trips.
I would like to see designs with and without the photo.
Colors I use are black (#000000), green (#25A796) and brown (#D7C38C)
Website satchelandsundial.example

Target Market(s)

location independent entrepreneurs, digital nomads, people looking to swap the 9 to 5 for a lifestyle business

Industry/Entity Type

Business

Contact Information for Business Card

Dorota Falkner
Your Lifestyle Business Coach, Retreat & Trip Leader
http://satchelandsundial.example
hello@satchelandsundial.example
Live a life you don't need a holiday from

Font styles to use
Serif
Sans Serif

Requirements
Must have
• One side should contain only the logo. I would also consider having the "Live a life you don't need a holiday from" on that side too (depending on how it looks)
• Please show both sides on the designs.

```html
<!DOCTYPE html>
<html lang="en">
<head>
<meta charset="utf-8">
<title>Satchel &amp; Sundial – Business Card</title>
<link rel="stylesheet" href="https://fonts.googleapis.com/css2?family=Oswald:wght@300;400;500&display=swap">
<style>
  :root {
    --backdrop: #e4e4e4;
    --card-white: #fbfbfb;
    --card-white-edge: #ececec;
    --ink: #111111;
    --card-dark: #1e2022;
    --teal: #25a796;
    --teal-text: #2a9d86;
    --sand: #d7c38c;
    --light: #f2f2f2;
    --photo-light: #a9b48a;
    --photo-dark: #4d5a3a;
  }
  * { margin: 0; padding: 0; box-sizing: border-box; }
  html, body {
    width: 1200px; height: 576px; overflow: hidden;
    background: var(--backdrop);
    font-family: "Oswald", "Arial Narrow", sans-serif;
  }
  .canvas { position: relative; width: 1200px; height: 576px; }

  .card {
    position: absolute; top: 138px;
    width: 484px; height: 294px;
    border-radius: 9px; overflow: hidden;
    box-shadow: 1px 3px 6px rgba(0,0,0,.25);
  }

  /* Logo side */
  .card--front {
    left: 82px;
    background: linear-gradient(180deg, var(--card-white) 0%, var(--card-white-edge) 100%);
  }
  .brand-name {
    position: absolute; left: 0; right: 0; top: 98px;
    text-align: center;
    font-weight: 400; font-size: 42px; letter-spacing: 1px;
    text-transform: uppercase; color: var(--ink);
  }
  .front-url {
    position: absolute; left: 0; right: 0; top: 251px;
    display: flex; justify-content: center; align-items: center; gap: 14px;
    font-size: 12px; font-weight: 400; color: var(--ink);
  }
  .front-url .domain { color: var(--teal-text); }
  .front-url .rule { width: 44px; height: 2px; background: var(--sand); border-radius: 2px; }

  /* Contact side */
  .card--back { left: 602px; background: var(--card-dark); }
  .card--back svg.art { position: absolute; inset: 0; }
  .contact {
    position: absolute; right: 26px; top: 0; bottom: 0;
    text-align: right; color: var(--light);
  }
  .contact__name {
    position: absolute; right: 0; top: 34px; white-space: nowrap;
    font-size: 21px; font-weight: 500; text-transform: uppercase; color: var(--sand);
  }
  .contact__role {
    position: absolute; right: 0; top: 64px; white-space: nowrap;
    font-size: 11.5px; font-weight: 300; line-height: 15px;
  }
  .contact__list {
    position: absolute; right: 0; top: 154px; list-style: none;
    font-size: 12px; font-weight: 300; line-height: 21px; white-space: nowrap;
  }
  .contact__list li { display: flex; justify-content: flex-end; align-items: center; gap: 7px; }
  .contact__list svg { width: 11px; height: 11px; }
  .contact__tagline {
    position: absolute; right: 0; top: 237px; white-space: nowrap;
    font-size: 14px; font-weight: 400; color: var(--teal-text);
  }
</style>
</head>
<body>
<main class="canvas">

  <section class="card card--front" aria-label="Logo side">
    <h1 class="brand-name">Satchel &amp; Sundial</h1>
    <p class="front-url">
      <span class="rule"></span>
      <span>www.<span class="domain">satchelandsundial</span>.example</span>
      <span class="rule"></span>
    </p>
  </section>

  <section class="card card--back" aria-label="Contact side">
    <svg class="art" viewBox="0 0 484 294" width="484" height="294">
      <defs>
        <linearGradient id="photoTone" x1="0" y1="0" x2="1" y2="1">
          <stop offset="0" stop-color="var(--photo-light)"/>
          <stop offset="0.55" stop-color="#7f8c63"/>
          <stop offset="1" stop-color="var(--photo-dark)"/>
        </linearGradient>
      </defs>
      <path role="img" aria-label="Photo of the coach seated outdoors among trees, holding a small sign"
            d="M0,0 H192 Q272,147 186,294 H0 Z" fill="url(#photoTone)"/>
      <path class="accent-arc" d="M158,0 H176 Q266,112 214,236 Q244,108 158,0 Z" fill="var(--teal)"/>
    </svg>

    <div class="contact">
      <h2 class="contact__name">Dorota Falkner</h2>
      <p class="contact__role">Your Lifestyle Business Coach<br>Retreat &amp; Trip Leader</p>
      <ul class="contact__list">
        <li>hello@satchelandsundial.example
          <svg viewBox="0 0 12 12"><rect x="0.5" y="2" width="11" height="8" fill="var(--teal)"/><path d="M0.5,2 L6,6.5 L11.5,2" fill="none" stroke="var(--card-dark)" stroke-width="1"/></svg>
        </li>
        <li>www.satchelandsundial.example
          <svg viewBox="0 0 12 12"><circle cx="6" cy="6" r="5" fill="none" stroke="var(--teal)" stroke-width="1.2"/><ellipse cx="6" cy="6" rx="2.2" ry="5" fill="none" stroke="var(--teal)" stroke-width="1"/><path d="M1,6 H11" stroke="var(--teal)" stroke-width="1"/></svg>
        </li>
        <li>/satchelandsundial
          <svg viewBox="0 0 12 12"><rect x="1" y="1" width="10" height="10" rx="2" fill="var(--teal)"/></svg>
        </li>
      </ul>
      <p class="contact__tagline">Live a life you don’t need a holiday from</p>
    </div>
  </section>

</main>
</body>
</html>
```